Zelvo Stationary

Design the stationary of Zelvo Promotions Group.

Zelvo is a BTL company, BTL meaning "below the line". In other words Zelvo is a Promotional Marketing company (the company that design the brands promotional activities).

The design should transmit creativity, agility, boldness.

I need:
* Bis Card
* Letter head
* Envelopes, both vertical and horizontal (for legal size), and letter envelope
* Folders
* PPT template (Title page and regular page)
* CD slip (CD envelope)
* ID card (employee card)

And what ever else you want to throw in.
Updates

Guys,

Something I missed from the brief.   The predominat color should be RED.

Also, have fun and play with the exclamation mark (!) of the logo. 

Hi guys, more comments:

Remember that Zelvo is a "creativity" agency, not in the advertising side but on the promotional side, and that should reflect on the stationary.

 I want a bold design.  Bold and yet crisp.

 

Guys, i just uploaded the Logo in AI format.

I Also uploaded the actual Zelvo Bis Card, wich I like.  So I will like to see some designs with that bis card approach.

Guys, I am so sorry, but I notice in your last post that I upladed a wrong design ("13154_promotions_group_zelvo_brief225630.ai").  The problem was that I asked the designer the file in AI format and he send me thw wrong file, and since I dont have Illustrator I could not verify it.

The differences are minor, I just already ask him the correct one (similar to the EPS file).

Sorry                                   

Just post the correct AI file : "Zelvo Logo.ai"

Reason: I'm expecting more designs to choose from and also I wont be available tomorrow to decide.

Reason: Sorry guys, but we are not there yet!

Target Market(s)

Marketing directors, Marketing Managers

Industry/Entity Type

Legal

Requirements
Must have
• Must work with the logo attached.
The predominat color should be RED.
Play and have fun with the exclamation mark (!).
Should not have
• * No old fonts

Should not be:
* boring
* Informal
* rigid

```html
<!DOCTYPE html>
<html lang="es">
<head>
<meta charset="utf-8">
<title>Zelvo Promotions Group — Letterhead</title>
<link rel="stylesheet" href="https://fonts.googleapis.com/css2?family=Montserrat:wght@600;800&display=swap">
<style>
  :root {
    --red-deep: #560006;
    --red-mid: #7d0710;
    --red-bright: #a2111a;
    --ink: #111111;
    --accent: #d0141f;
    --paper: #ffffff;
    --footer-text: #ffffff;
  }
  html, body {
    margin: 0;
    padding: 0;
    width: 848px;
    height: 1200px;
    overflow: hidden;
    background: var(--paper);
  }
  .letterhead {
    position: relative;
    width: 848px;
    height: 1200px;
    overflow: hidden;
    background: var(--paper);
    font-family: "Montserrat", sans-serif;
  }
  .letterhead__bands {
    position: absolute;
    inset: 0;
  }
  .brand {
    position: absolute;
    left: 31px;
    top: 100px;
    display: flex;
    align-items: center;
    gap: 10px;
    color: var(--ink);
  }
  .brand__name {
    font-weight: 800;
    font-size: 40px;
    line-height: 1;
    letter-spacing: -0.5px;
  }
  .brand__sub {
    display: block;
    font-weight: 800;
    font-size: 10.5px;
    letter-spacing: 3px;
    margin-top: 6px;
    text-transform: uppercase;
  }
  .brand__dot {
    width: 26px;
    height: 26px;
    border-radius: 50%;
    background: var(--accent);
    align-self: flex-end;
    margin-bottom: 6px;
  }
  .contact {
    position: absolute;
    left: 31px;
    top: 1110px;
    color: var(--footer-text);
  }
  .contact__address {
    margin: 0;
    font-weight: 600;
    font-size: 11.5px;
    line-height: 14px;
  }
  .contact__web {
    display: block;
    margin-top: 8px;
    margin-left: 3px;
    font-weight: 600;
    font-size: 19px;
    color: var(--footer-text);
    text-decoration: none;
    letter-spacing: 0.3px;
  }
</style>
</head>
<body>
  <main class="letterhead">
    <svg class="letterhead__bands" width="848" height="1200" viewBox="0 0 848 1200" aria-hidden="true">
      <defs>
        <linearGradient id="band-gradient" x1="0" y1="0" x2="1" y2="0">
          <stop offset="0" stop-color="var(--red-deep)"/>
          <stop offset="0.5" stop-color="var(--red-bright)"/>
          <stop offset="1" stop-color="var(--red-deep)"/>
        </linearGradient>
      </defs>
      <path class="band band--top" d="M0,0 H848 V303 C720,185 430,52 0,40 Z" fill="url(#band-gradient)"/>
      <circle class="band__mark" cx="750" cy="165" r="30" fill="#ffffff" opacity="0.14"/>
      <path class="band band--bottom" d="M0,914 C170,1080 480,1162 848,1178 V1200 H0 Z" fill="url(#band-gradient)"/>
    </svg>

    <header class="brand">
      <div>
        <span class="brand__name">Zelvo</span>
        <span class="brand__sub">Promotions Group</span>
      </div>
      <span class="brand__dot"></span>
    </header>

    <footer class="contact">
      <p class="contact__address">
        Calle Marbella 18, Ens. Los Robles, Santo Domingo,<br>
        República Dominicana<br>
        Tel: 809.555.0148 &nbsp;|&nbsp; Fax: 809.555.0172
      </p>
      <a class="contact__web" href="#">www.zelvo.com.do</a>
    </footer>
  </main>
</body>
</html>
```